Music Marketing Agency in need of a fully responsive website

Need a website for our music marketing agency with a nice Rev slider has the ability to take payments has a section with our work and client able to see case studies able to download our media kit in PDF can take appointments has social media and a careers upload section. Also want a prominent contact form. Nice and icons for music industry. I want them to be able to download a free Picsandra marketing download Very clean and not large icons or menu at the top very minimal menu bar this will have to go with our logo as well which I will add to order. I want this to be a membership oriented site. so there will be packages displayed or a membership form which they can use to sign up and need a login window. Also need to be able to put Tunevox playlist on the website. Save a section for past clients logos.Again this has to be a clean concept I would like pictures of Quellos such as an app promotion. Definitely want lots of flash words in bold letters across the pages when they scroll through new sections.
Updates

Need extra days to review

Target Market(s)

Urban Music

Coding

Coded - Design and coding required

Font styles to use
Serif

Colors

Designer to choose colors to be used in the design.

Requirements
Must have
• Please Add Logos attached at the Footer

```html
<!DOCTYPE html>
<html lang="en">
<head>
<meta charset="utf-8">
<title>Northlane Sound – Member Login</title>
<link href="https://fonts.googleapis.com/css2?family=Montserrat:wght@400;500;600;700&family=Open+Sans:wght@400&display=swap" rel="stylesheet">
<style>
  :root {
    --bg-deep: #140a10;
    --bg-plum: #3e1c32;
    --bg-rose: #6a3456;
    --bg-amber: #4a2616;
    --panel: rgba(14, 7, 11, 0.9);
    --white: #ffffff;
    --btn-top: #ffa412;
    --btn-bottom: #ff6a00;
    --field-line: rgba(255, 255, 255, 0.55);
    --footer-bg: #000000;
    --footer-text: #8a8a8a;
  }
  * { box-sizing: border-box; margin: 0; padding: 0; }
  html, body { width: 1200px; height: 752px; overflow: hidden; }
  body {
    position: relative;
    font-family: "Montserrat", sans-serif;
    color: var(--white);
    background: var(--bg-deep);
  }
  .stage-backdrop {
    position: absolute; inset: 0;
    background:
      radial-gradient(ellipse at 82% 18%, rgba(190,110,150,0.45), transparent 55%),
      radial-gradient(ellipse at 18% 35%, rgba(140,85,35,0.35), transparent 50%),
      radial-gradient(ellipse at 70% 60%, rgba(120,40,100,0.4), transparent 60%),
      linear-gradient(165deg, var(--bg-amber), var(--bg-plum) 45%, var(--bg-rose) 65%, var(--bg-deep) 95%);
  }
  .brand {
    position: absolute; left: 0; right: 0; top: 126px;
    text-align: center;
    font-weight: 700; font-size: 37px; letter-spacing: 0.3px;
    color: var(--white);
  }
  .login-panel {
    position: absolute; left: 400px; top: 215px;
    width: 408px; height: 322px;
    background: var(--panel);
    padding-top: 34px;
  }
  .login-title {
    text-align: center; font-weight: 600; font-size: 28px;
    letter-spacing: 0.3px; line-height: 30px;
  }
  .login-field {
    position: absolute; left: 37px; width: 337px; height: 40px;
    border: 1px solid var(--field-line);
    padding-left: 22px;
    display: flex; align-items: center;
    font-size: 16px; font-weight: 500;
  }
  .field-username { top: 90px; }
  .field-password { top: 141px; }
  .login-button {
    position: absolute; left: 39px; top: 195px; width: 334px; height: 50px;
    background: linear-gradient(var(--btn-top), var(--btn-bottom));
    color: var(--white);
    font-weight: 700; font-size: 18px;
    display: flex; align-items: center; justify-content: center;
  }
  .forgot-link {
    position: absolute; left: 0; right: 0; top: 264px;
    text-align: center; font-size: 14px; font-weight: 500;
  }
  .site-footer {
    position: absolute; left: 0; right: 0; bottom: 0; height: 60px;
    background: var(--footer-bg);
    display: flex; align-items: center; justify-content: center;
    font-family: "Open Sans", sans-serif; font-size: 13px; color: var(--footer-text);
    word-spacing: 1px;
  }
</style>
</head>
<body>
  <div class="stage-backdrop" role="img" aria-label="Live concert photo: guitarist on stage under warm stage lights with a crowd in the foreground"></div>

  <h1 class="brand">NORTHLANE SOUND</h1>

  <section class="login-panel">
    <h2 class="login-title">LOGIN MEMBER</h2>
    <div class="login-field field-username">Username</div>
    <div class="login-field field-password">Password</div>
    <div class="login-button">LOGIN</div>
    <div class="forgot-link">Forget Password?</div>
  </section>

  <footer class="site-footer">© 2018 Company Name &nbsp;All right reserved &nbsp;Terms of Use</footer>
</body>
</html>
```